VOMRA Pty Ltd Business Card

Looking for a simple yet eye-catching double-sided business card design using my company logo on one side and contact details on the other.

Target Market(s)

Government

Industry/Entity Type

Communication Systems Engineering

Contact Information for Business Card

VOMRA Pty Ltd

Requirements
Nice to have
• Would be great to have a QR code so details can be scanned into contacts

```html
<!DOCTYPE html>
<html lang="en">
<head>
<meta charset="utf-8">
<title>VOMRA Pty Ltd Business Card</title>
<link href="https://fonts.googleapis.com/css2?family=Open+Sans:wght@400;700&display=swap" rel="stylesheet">
<style>
  :root {
    --backdrop: #e4e4e2;
    --slate: #313b43;
    --slate-deep: #252e35;
    --paper: #ececec;
    --ink: #111418;
    --light-text: #e8eaec;
    --circuit-tone: #8a9196;
  }
  * { margin: 0; padding: 0; box-sizing: border-box; }
  html, body { width: 1200px; height: 780px; overflow: hidden; }
  body {
    background: var(--backdrop);
    font-family: "Open Sans", Arial, sans-serif;
    position: relative;
  }
  .card {
    position: absolute;
    top: 235px;
    width: 540px;
    height: 310px;
    overflow: hidden;
  }
  .card--front { left: 40px; background: var(--paper); }
  .card--back { left: 620px; background: var(--slate); }

  .front-brand {
    position: absolute;
    left: 36px;
    top: 34px;
    display: flex;
    align-items: center;
    gap: 14px;
  }
  .brand-dot {
    width: 34px; height: 34px;
    border-radius: 50%;
    background: var(--slate);
  }
  .brand-name {
    font-weight: 700;
    font-size: 40px;
    letter-spacing: 4px;
    color: var(--slate);
    line-height: 1;
  }
  .contact-band {
    position: absolute;
    left: 0; top: 130px;
    width: 380px; height: 180px;
    background: var(--slate);
  }
  .contact-list {
    list-style: none;
    position: absolute;
    left: 18px; top: 14px;
    color: var(--light-text);
    font-size: 12px;
    line-height: 17px;
  }
  .contact-list li { display: flex; align-items: center; gap: 6px; }
  .contact-icon { width: 10px; height: 10px; flex: none; }
  .circuit-art {
    position: absolute;
    left: 300px; top: 196px;
    width: 170px; height: 114px;
    border-radius: 50% 50% 0 0;
    background: radial-gradient(ellipse at 50% 60%, var(--circuit-tone), rgba(138,145,150,0.35) 70%, rgba(138,145,150,0) 100%);
  }
  .holder {
    position: absolute;
    right: 30px; top: 72px;
    text-align: right;
    color: var(--ink);
  }
  .holder-name { font-weight: 700; font-size: 25px; line-height: 1.1; }
  .holder-role { font-size: 13px; margin-top: 2px; }
  .edge-tab {
    position: absolute;
    right: 0; top: 112px;
    width: 14px; height: 40px;
    background: var(--slate);
  }

  .back-brand {
    position: absolute;
    left: 50%; top: 50%;
    transform: translate(-50%, -50%);
    display: flex;
    align-items: center;
    gap: 18px;
  }
  .back-brand .brand-dot { width: 46px; height: 46px; background: var(--slate-deep); }
  .back-brand .brand-name { font-size: 58px; color: var(--slate-deep); letter-spacing: 6px; }
</style>
</head>
<body>
  <section class="card card--front" aria-label="Business card, contact side">
    <div class="front-brand">
      <span class="brand-dot"></span>
      <span class="brand-name">VOMRA</span>
    </div>
    <div class="contact-band">
      <ul class="contact-list">
        <li>27-29 Larkin Street Ashgrove</li>
        <li>NSW 2040 Australia</li>
        <li>
          <svg class="contact-icon" viewBox="0 0 10 10"><path d="M2 1 L4 1 L4.6 3 L3.4 4 Q4.2 5.8 6 6.6 L7 5.4 L9 6 L9 8 Q5 9 1.6 5 Q1 3 2 1Z" fill="currentColor"/></svg>
          (555) 014-2273
        </li>
        <li>
          <svg class="contact-icon" viewBox="0 0 10 10"><circle cx="5" cy="5" r="4" fill="none" stroke="currentColor" stroke-width="1"/><path d="M1 5 H9 M5 1 V9" stroke="currentColor" stroke-width="0.8"/></svg>
          www.vomra.com.au
        </li>
        <li>
          <svg class="contact-icon" viewBox="0 0 10 10"><rect x="1" y="2.5" width="8" height="5.5" fill="none" stroke="currentColor" stroke-width="1"/><path d="M1 2.5 L5 5.8 L9 2.5" fill="none" stroke="currentColor" stroke-width="1"/></svg>
          admin@vomra.com.au
        </li>
      </ul>
    </div>
    <div class="circuit-art" role="img" aria-label="Decorative circuit-board tree illustration"></div>
    <div class="holder">
      <p class="holder-name">Jordan Hale</p>
      <p class="holder-role">Co-Founder</p>
    </div>
    <span class="edge-tab"></span>
  </section>

  <section class="card card--back" aria-label="Business card, brand side">
    <div class="back-brand">
      <span class="brand-dot"></span>
      <span class="brand-name">VOMRA</span>
    </div>
  </section>
</body>
</html>
```